Need wine label for brand that is named: Kesavati Vineyards & Winery

Kesavati is a yoga way of breathing. In Sanskrit Kesavati means "flying up." I would like a creative wine label that articulates Kesavati. The label should include a graphic and the name Kesavati on one line and Vineyards & Winery in smaller print underneath Kesavati.

```html
<!DOCTYPE html>
<html lang="en">
<head>
<meta charset="utf-8">
<title>Kesavati Vineyards &amp; Winery — Pinot Noir 2014</title>
<link rel="stylesheet" href="https://fonts.googleapis.com/css2?family=Cormorant+Garamond:wght@500;600&display=swap">
<style>
  :root {
    --bg-top: #2b2b30;
    --bg-bottom: #121214;
    --gold: #c9954f;
    --gold-light: #e2b878;
    --gold-deep: #8a5e2a;
    --silver: #cfcfd2;
    --ivory: #f2f0ec;
    --muted: #bdbdc0;
  }
  * { margin: 0; padding: 0; box-sizing: border-box; }
  html, body { width: 943px; height: 1200px; overflow: hidden; background: var(--bg-bottom); }
  .label {
    position: relative;
    width: 943px;
    height: 1200px;
    overflow: hidden;
    background: radial-gradient(ellipse 80% 60% at 50% 45%, var(--bg-top), var(--bg-bottom));
    font-family: "Cormorant Garamond", Georgia, serif;
    color: var(--ivory);
    text-align: center;
  }
  .mandala-field { position: absolute; left: 0; top: 0; width: 943px; height: 560px; }
  .brand {
    position: absolute;
    left: 0; right: 0; top: 92px;
    font-size: 132px;
    font-weight: 600;
    line-height: 1;
    color: var(--ivory);
    letter-spacing: 2px;
  }
  .brand-band {
    position: absolute;
    left: 68px; width: 820px; top: 226px; height: 56px;
    background: linear-gradient(90deg, rgba(201,149,79,0.35), rgba(20,20,22,0.88) 40%, rgba(20,20,22,0.88) 60%, rgba(201,149,79,0.35));
    border-bottom: 3px solid var(--gold);
    display: flex; align-items: center; justify-content: center;
  }
  .brand-sub {
    font-size: 28px;
    font-weight: 500;
    letter-spacing: 16px;
    margin-right: -16px;
    text-transform: uppercase;
    color: var(--ivory);
  }
  .varietal {
    position: absolute; left: 0; right: 0; top: 556px;
    font-size: 84px; font-weight: 500; color: var(--silver);
  }
  .divider-mark { position: absolute; left: 459px; top: 711px; width: 26px; height: 26px; }
  .vintage {
    position: absolute; left: 0; right: 0; top: 802px;
    font-size: 48px; font-weight: 500; letter-spacing: 11px; margin-right: -11px; color: var(--muted);
  }
  .series {
    position: absolute; left: 0; right: 0; top: 886px;
    font-size: 52px; font-weight: 600; letter-spacing: 10px; margin-right: -10px; text-transform: uppercase;
    background: linear-gradient(180deg, var(--gold-light), var(--gold) 55%, var(--gold-deep));
    -webkit-background-clip: text; background-clip: text; color: transparent;
  }
  .appellation {
    position: absolute; left: 0; right: 0; top: 982px;
    font-size: 39px; font-weight: 500; color: var(--ivory);
  }
  .abv {
    position: absolute; left: 0; right: 0; top: 1128px;
    font-size: 24px; font-weight: 500; letter-spacing: 6px; margin-right: -6px; color: var(--muted);
  }
</style>
</head>
<body>
<main class="label">
  <svg class="mandala-field" viewBox="0 0 943 560" role="img" aria-label="Gold ornamental mandala fanning down from the top edge, symbolising breath flying upward">
    <defs>
      <radialGradient id="mandalaFill" cx="472" cy="-20" r="550" gradientUnits="userSpaceOnUse">
        <stop offset="0" stop-color="#9a6d38"/>
        <stop offset="0.45" stop-color="#6f5132"/>
        <stop offset="0.85" stop-color="#4a3b2d"/>
        <stop offset="1" stop-color="#3a3029"/>
      </radialGradient>
    </defs>
    <circle cx="472" cy="-20" r="550" fill="url(#mandalaFill)"/>
  </svg>

  <h1 class="brand">Kesavati</h1>
  <div class="brand-band"><p class="brand-sub">Vineyards &amp; Winery</p></div>

  <h2 class="varietal">Pinot Noir</h2>
  <svg class="divider-mark" viewBox="0 0 26 26" role="img" aria-label="Small gold ornament">
    <circle cx="13" cy="13" r="12" fill="#b98544"/>
  </svg>
  <p class="vintage">2014</p>
  <p class="series">Collection</p>
  <p class="appellation">Napa Valley</p>
  <p class="abv">11.8% alc/vol.</p>
</main>
</body>
</html>
```